Stationary Design for Quince consultant and support company

We need new stationary designed for a London based support company that provide on-site and remote support services for Quince products. Our clients are both consumers and businesses.

We would like a letterhead, compliment slip, business card and possibly an e-mail signature designed.

Business card designs can be either 1 side or 2, depending on designs we receive we may choose a preference for 1 or 2 sides later on in the design stage.

Designs needs to be at least 300dpi and should be done using CMYK colours.

We want the design to be bold, easy to read, clean and professional.

We have attached our company logo in 2 colour variations (if you need any other source files then please ask).

Our logo colours are as follows:

Blue (85, 50, 0, 0) and Green (50, 0, 100, 0)

We use two different suppliers for out stationary so here are the size dimensions for both. Unfortunately they are ever so slightly different size wise so hopefully we can get something that accommodates both, we can provide dimensions if required for final versions.

Some fonts that have been used before with our company are Probert (for tagline on our company logo) and previously had Nauman used, however we are very much open to seeing what the designers come up with and the fonts mentioned are not a requirement.
Updates

Company details for designs (however the template should be editable for multiple staff) Lumora Ltd. Registered Office: 62-70 Harrowfield Lane London N7 3QD 020 7591 3384 www.lumora-it.example info@lumora-it.example Company is Registered in England and Wales Company No. 07342519 Directors details (if you want to make the template using his details), rest of the details are as above Dan Frost Director dan@lumora-it.example

Hi all, Thank you for your submissions so far. Could we please ask that you don't use the logo with the tagline from our website for the stationary designs and only the logos provided in the design brief. For the business cards we are looking at normal rectangular business cards to be used and we can provide a template guide for size if needed, please just ask. Regards Lumora Team

Target Market(s)

Our target market are consumers (of all ages) and small/medium businesses.

Industry/Entity Type

Business

Font styles to use
Serif
Sans Serif

Requirements
Must have
• At least business card, letterhead and compliment slip submitted (we need all 3 designed this time round)
Should not have
• Business cards should not have the writing "registered office" (letterheads and compliment slips can along the bottom edge)

```html
<!DOCTYPE html>
<html lang="en">
<head>
<meta charset="utf-8">
<title>Lumora – Business Card</title>
<link rel="stylesheet" href="https://fonts.googleapis.com/css2?family=Open+Sans:wght@300;400;600;700&display=swap">
<style>
  :root {
    --backdrop: #d4e5f2;
    --card: #ffffff;
    --brand-blue: #3a82c0;
    --brand-green: #8cc652;
    --ink: #3a3a3a;
    --ink-soft: #555555;
  }
  html, body {
    margin: 0;
    padding: 0;
    width: 1200px;
    height: 1000px;
    overflow: hidden;
    background: var(--backdrop);
    font-family: "Open Sans", Arial, sans-serif;
  }
  .business-card {
    position: absolute;
    left: 100px;
    top: 214px;
    width: 1000px;
    height: 572px;
    background: var(--card);
    box-shadow: 0 6px 18px rgba(40, 70, 100, 0.18);
    overflow: hidden;
  }
  .colour-band {
    position: absolute;
    top: 0;
    height: 572px;
  }
  .colour-band--blue {
    left: 0;
    width: 300px;
    background: var(--brand-blue);
  }
  .colour-band--green {
    left: 330px;
    width: 48px;
    background: var(--brand-green);
  }

  .company-name {
    position: absolute;
    left: 500px;
    top: 250px;
    margin: 0;
    font-size: 46px;
    font-weight: 700;
    letter-spacing: 1px;
    color: var(--ink);
    line-height: 1;
  }
  .contact-block {
    position: absolute;
    left: 730px;
    top: 240px;
    color: var(--ink);
  }
  .person-name {
    margin: 0;
    font-size: 30px;
    font-weight: 600;
    line-height: 1.1;
  }
  .person-role {
    margin: 0 0 10px;
    font-size: 24px;
    font-weight: 300;
    color: var(--ink-soft);
    line-height: 1.2;
  }
  .contact-line {
    margin: 0;
    font-size: 15px;
    font-weight: 400;
    color: var(--ink-soft);
    line-height: 1.5;
  }
</style>
</head>
<body>
  <main class="business-card">
    <div class="colour-band colour-band--blue" aria-hidden="true"></div>
    <div class="colour-band colour-band--green" aria-hidden="true"></div>

    <h1 class="company-name">Lumora</h1>

    <section class="contact-block">
      <p class="person-name">Dan Frost</p>
      <p class="person-role">Director</p>
      <p class="contact-line">020 7591 3384</p>
      <p class="contact-line">www.lumora-it.example</p>
      <p class="contact-line">dan@lumora-it.example</p>
    </section>
  </main>
</body>
</html>
```